Insurance Agency website design for Brellow Cover Insurance, LP

Build a website for Brellow Cover Insurance, LP which sells Homeowners, Auto, Renters, Condo, Flood, Disability, Life, Umbrella, and health insurance. We need the coolest insurance agency website out there to get quotes, contact us, or get additional information. Please list the following insurance companies we work with: Varnix, Ostle, Meridale Mutual, Quillor, Dunmarrow, KGZ, and Pellwick.

Make a design similar to https://www.fernagentry.com/

Selling personal insurance policies

```html
<!DOCTYPE html>
<html lang="en">
<head>
<meta charset="utf-8">
<title>Brellow Cover Insurance LP</title>
<link href="https://fonts.googleapis.com/css2?family=Montserrat:wght@600;700;800&family=Open+Sans:wght@400;600;700&display=swap" rel="stylesheet">
<style>
:root{
  --navy:#0b3a78;
  --navy-deep:#082a5a;
  --green:#2e9a3a;
  --green-dark:#237a2d;
  --ink:#1d2330;
  --text:#4a5160;
  --muted:#8a909b;
  --light:#f2f3f5;
  --band:#e9eaec;
  --white:#ffffff;
  --head:"Montserrat",sans-serif;
  --body:"Open Sans",sans-serif;
}
*{box-sizing:border-box;margin:0;padding:0}
html,body{width:1200px;height:3000px;overflow:hidden}
body{font-family:var(--body);color:var(--text);background:var(--white);position:relative}
a{color:inherit;text-decoration:none}
.btn{display:inline-block;background:var(--green);color:var(--white);font-family:var(--head);font-weight:700;font-size:14px;letter-spacing:.5px;padding:13px 28px;border-radius:28px}

/* top bar + header */
.topbar{position:absolute;top:0;left:0;width:1200px;height:36px;display:flex;align-items:center;justify-content:flex-end;padding-right:60px;gap:26px;font-size:13px;color:var(--ink)}
.topbar .contact{display:flex;align-items:center;gap:8px}
.socials{position:absolute;left:50%;transform:translateX(-50%);top:4px;display:flex;gap:8px}
.socials span{width:28px;height:28px;border-radius:50%;background:var(--green);display:block}
.header{position:absolute;top:36px;left:0;width:1200px;height:104px;display:flex;align-items:center;padding:0 100px}
.nav{display:flex;gap:34px;font-family:var(--head);font-weight:700;font-size:14px;color:var(--ink);align-items:center}
.nav .active{background:var(--navy);color:var(--white);padding:10px 14px;border-radius:4px}
.nav.right{margin-left:auto}
.brand{position:absolute;left:50%;transform:translateX(-50%);top:14px;text-align:center;font-family:var(--head);font-weight:800;color:var(--navy);line-height:1}
.brand .name{font-size:34px}
.brand .sub{font-size:15px;letter-spacing:3px;margin-top:4px}

/* hero */
.hero{position:absolute;top:140px;left:0;width:1200px;height:610px;overflow:hidden}
.hero-media{position:absolute;inset:0;background:radial-gradient(circle at 72% 45%,#4aa3e0 0%,#1d5ea6 22%,#0b3a78 55%,#061d42 100%)}
.hero-copy{position:absolute;left:110px;top:105px;width:430px;color:var(--white)}
.hero-copy h1{font-family:var(--head);font-weight:800;font-size:46px;line-height:1.12;margin-bottom:22px}
.hero-copy p{font-size:16px;line-height:1.55;margin-bottom:30px}
.arrow{position:absolute;width:40px;height:40px;border-radius:50%;background:var(--white);display:flex;align-items:center;justify-content:center}
.hero .arrow.l{left:30px;top:240px}
.hero .arrow.r{right:30px;top:240px}
.hero-curve{position:absolute;left:0;bottom:0}
.dots{display:flex;gap:8px;justify-content:center}
.dots i{width:9px;height:9px;border-radius:50%;background:#c4c8ce;display:block}
.dots i.on{background:var(--navy)}
.hero .dots{position:absolute;left:0;right:0;top:560px}

/* about */
.about{position:absolute;top:820px;left:0;width:1200px;height:480px}
.about-frame{position:absolute;left:105px;top:0;width:160px;height:160px;border:5px solid var(--navy);border-right:none;border-bottom:none;border-radius:34px 0 0 0}
.about-photo{position:absolute;left:125px;top:20px;width:370px;height:450px;border-radius:40px;background:linear-gradient(135deg,#e9e2d6 0%,#c8b9a2 45%,#8a7a68 100%)}
.about-copy{position:absolute;left:665px;top:40px;width:420px}
.title{font-family:var(--head);font-weight:800;font-size:44px;line-height:1}
.title .a{color:var(--navy)}
.title .b{color:var(--green)}
.about-copy .title{font-size:40px;margin-bottom:22px}
.about-copy p{font-size:14px;line-height:1.6;margin-bottom:14px;color:var(--text)}
.about-copy .btn{margin-top:16px}

/* services */
.services{position:absolute;top:1395px;left:0;width:1200px;height:430px;background:var(--band)}
.services .title{text-align:center;margin-top:72px}
.cards{position:absolute;top:170px;left:110px;display:flex;gap:32px}
.card{width:222px;height:192px;background:var(--white);border-radius:22px;box-shadow:0 6px 18px rgba(0,0,0,.08);display:flex;flex-direction:column;align-items:center;justify-content:center;gap:22px}
.card.active{border:3px solid var(--green)}
.card span{font-family:var(--head);font-weight:800;font-size:17px;color:var(--navy)}
.services .arrow{top:248px;background:var(--navy)}
.services .arrow.l{left:36px;background:#c7ccd4}
.services .arrow.r{right:36px}

/* partners */
.partners{position:absolute;top:1855px;left:0;width:1200px;height:340px}
.partners .title{text-align:center;margin-top:50px}
.logos{position:absolute;top:148px;left:108px;display:flex;gap:30px}
.logo{width:176px;height:86px;background:var(--white);border-radius:14px;box-shadow:0 4px 16px rgba(0,0,0,.1);display:flex;align-items:center;justify-content:center;font-family:var(--head);font-weight:700;font-size:16px;color:var(--navy);text-align:center;padding:0 8px}
.partners .dots{position:absolute;left:0;right:0;top:280px}

/* cta */
.cta{position:absolute;top:2222px;left:0;width:1200px;height:478px}
.cta-panel{position:absolute;left:0;top:0;width:600px;height:478px;background:var(--navy);color:var(--white);padding:80px 110px 0 110px}
.cta-panel h2{font-family:var(--head);font-weight:800;font-size:42px;line-height:1.1;margin-bottom:22px}
.cta-panel h2 .b{color:#7ed957}
.cta-panel p{font-size:14px;line-height:1.6;margin-bottom:28px}
.cta-media{position:absolute;left:600px;top:0;width:600px;height:478px;background:radial-gradient(circle at 50% 48%,#5fd0f0 0%,#1c6fb0 30%,#0b2c5a 70%,#06193a 100%)}

/* footer */
.footer{position:absolute;top:2700px;left:0;width:1200px;height:260px;background:var(--light)}
.foot-brand{position:absolute;left:110px;top:100px;font-family:var(--head);font-weight:800;color:var(--navy);line-height:1}
.foot-brand .name{font-size:28px}
.foot-brand .sub{font-size:12px;letter-spacing:2.5px;margin-top:4px}
.col h4{font-family:var(--head);font-weight:800;font-size:16px;color:var(--navy);margin-bottom:16px}
.col{position:absolute;top:48px}
.col li{list-style:none;font-size:13px;color:var(--ink);margin-bottom:11px;display:flex;align-items:flex-start;gap:9px}
.col li svg{flex:none;margin-top:2px}
.col.company{left:375px}
.col.contact{left:530px;width:250px}
.col.news{left:805px;width:290px}
.news-form{display:flex;height:42px;background:var(--white);border-radius:22px;align-items:center;padding-left:18px;justify-content:space-between;margin-bottom:18px}
.news-form span{font-size:13px;color:var(--muted)}
.news-form b{background:var(--green);color:var(--white);font-family:var(--head);font-size:13px;padding:0 18px;height:42px;line-height:42px;border-radius:22px}
.news .socials{position:static;transform:none;justify-content:center}
.bottom{position:absolute;top:2960px;left:0;width:1200px;height:40px;border-top:1px solid #d7d9dd;text-align:center;font-size:12px;color:var(--ink);line-height:40px}
.bottom strong{font-family:var(--head)}
</style>
</head>
<body>

<div class="topbar">
  <div class="socials" aria-label="Social links"><span></span><span></span><span></span></div>
  <div class="contact">
    <svg width="14" height="14" viewBox="0 0 24 24"><path fill="#2e9a3a" d="M6.6 10.8a15.1 15.1 0 006.6 6.6l2.2-2.2a1 1 0 011-.25 11.4 11.4 0 003.6.6 1 1 0 011 1V20a1 1 0 01-1 1A17 17 0 013 4a1 1 0 011-1h3.5a1 1 0 011 1c0 1.25.2 2.45.6 3.6a1 1 0 01-.25 1z"/></svg>
    (555) 201-4486
  </div>
  <div class="contact">
    <svg width="15" height="12" viewBox="0 0 24 18"><rect x="1" y="1" width="22" height="16" rx="2" fill="#2e9a3a"/><path d="M2 2l10 8 10-8" stroke="#fff" stroke-width="2" fill="none"/></svg>
    info@brellowcover.com
  </div>
</div>

<header class="header">
  <nav class="nav">
    <a class="active">HOME</a><a>ABOUT US</a><a>WHAT WE DO</a>
  </nav>
  <div class="brand"><div class="name">BRELLOW COVER</div><div class="sub">INSURANCE LP</div></div>
  <nav class="nav right">
    <a>CONTACT US</a><a class="btn">GET A QUOTE</a>
  </nav>
</header>

<section class="hero">
  <div class="hero-media" role="img" aria-label="Hands holding a glowing shield icon above a house, on a deep blue background"></div>
  <div class="hero-copy">
    <h1>BRELLOW COVER INSURANCE LP</h1>
    <p>Brellow Cover Insurance is a full-service, independent insurance agency with over three decades of experience in delivering comprehensive insurance solutions to individuals.</p>
    <a class="btn">GET A QUOTE</a>
  </div>
  <div class="arrow l"><svg width="14" height="14" viewBox="0 0 14 14"><path d="M9 2L4 7l5 5" stroke="#0b3a78" stroke-width="2.4" fill="none"/></svg></div>
  <div class="arrow r"><svg width="14" height="14" viewBox="0 0 14 14"><path d="M5 2l5 5-5 5" stroke="#0b3a78" stroke-width="2.4" fill="none"/></svg></div>
  <svg class="hero-curve" width="1200" height="120" viewBox="0 0 1200 120"><path d="M0 120V70C300 130 700 120 1200 10V120Z" fill="#fff"/></svg>
  <div class="dots"><i></i><i class="on"></i><i></i><i></i></div>
</section>

<section class="about">
  <div class="about-frame"></div>
  <div class="about-photo" role="img" aria-label="Agent reviewing a policy with a couple at a table"></div>
  <div class="about-copy">
    <h2 class="title"><span class="a">ABOUT</span> <span class="b">US</span></h2>
    <p>Brellow Cover Insurance is a full-service, independent insurance agency with over three decades of experience in delivering comprehensive insurance solutions to individuals.</p>
    <p>We proudly offer a diverse portfolio of products from more than 20 of the most reputable and financially secure companies in the industry. Our dedicated team of over 50 skilled professionals is committed to customizing these products and services to meet the unique needs of each client.</p>
    <p>At Brellow Cover Insurance, our experts are focused on addressing the individual needs of our clients, ensuring exceptional service and support at every step.</p>
    <a class="btn">LEARN MORE</a>
  </div>
</section>

<section class="services">
  <h2 class="title"><span class="a">WHAT</span> <span class="b">WE DO</span></h2>
  <div class="arrow l"><svg width="14" height="14" viewBox="0 0 14 14"><path d="M9 2L4 7l5 5" stroke="#fff" stroke-width="2.4" fill="none"/></svg></div>
  <div class="arrow r"><svg width="14" height="14" viewBox="0 0 14 14"><path d="M5 2l5 5-5 5" stroke="#fff" stroke-width="2.4" fill="none"/></svg></div>
  <div class="cards">
    <div class="card">
      <svg width="64" height="64" viewBox="0 0 64 64"><path d="M8 30L32 10l24 20" stroke="#2e9a3a" stroke-width="5" fill="none" stroke-linejoin="round"/><path d="M15 27v27h34V27" stroke="#2e9a3a" stroke-width="5" fill="none"/><rect x="27" y="38" width="10" height="16" fill="#2e9a3a"/></svg>
      <span>HOMEOWNERS</span>
    </div>
    <div class="card">
      <svg width="70" height="60" viewBox="0 0 70 60"><path d="M10 34l6-16h38l6 16v14H10z" fill="#2e9a3a"/><rect x="20" y="22" width="30" height="9" rx="2" fill="#fff"/><circle cx="20" cy="48" r="6" fill="#fff" stroke="#2e9a3a" stroke-width="4"/><circle cx="50" cy="48" r="6" fill="#fff" stroke="#2e9a3a" stroke-width="4"/></svg>
      <span>AUTO</span>
    </div>
    <div class="card">
      <svg width="64" height="64" viewBox="0 0 64 64"><path d="M20 10l14-8 14 8v12H20z" fill="#2e9a3a"/><path d="M6 44h14l14 4h10a4 4 0 010 8H26" stroke="#2e9a3a" stroke-width="5" fill="none" stroke-linecap="round"/><path d="M40 44l14-8a4 4 0 014 6L44 54" stroke="#2e9a3a" stroke-width="5" fill="none" stroke-linecap="round"/></svg>
      <span>RENTERS</span>
    </div>
    <div class="card active">
      <svg width="64" height="64" viewBox="0 0 64 64"><circle cx="28" cy="9" r="6" fill="#2e9a3a"/><path d="M28 18v18h16l6 16" stroke="#2e9a3a" stroke-width="5" fill="none" stroke-linecap="round" stroke-linejoin="round"/><path d="M20 30a14 14 0 1020 18" stroke="#2e9a3a" stroke-width="5" fill="none" stroke-linecap="round"/></svg>
      <span>DISABILITY</span>
    </div>
  </div>
</section>

<section class="partners">
  <h2 class="title"><span class="a">TRUSTED</span> <span class="b">BY</span></h2>
  <div class="logos">
    <div class="logo">VARNIX</div>
    <div class="logo">PELLWICK</div>
    <div class="logo">Meridale Mutual</div>
    <div class="logo">DUNMARROW</div>
    <div class="logo">Quillor</div>
  </div>
  <div class="dots"><i></i><i class="on"></i><i></i></div>
</section>

<section class="cta">
  <div class="cta-panel">
    <h2>GET READY <span class="b">TO</span><br>START?</h2>
    <p>We believe that securing your home is one of the most important decisions you can make. Obtaining a comprehensive insurance quote is essential to understanding your coverage options and ensuring that your property is adequately protected against unforeseen events.</p>
    <a class="btn">GET A QUOTE</a>
  </div>
  <div class="cta-media" role="img" aria-label="Hand holding glowing icons of a family, home and car under a protective shield"></div>
</section>

<footer class="footer">
  <div class="foot-brand"><div class="name">BRELLOW COVER</div><div class="sub">INSURANCE LP</div></div>
  <div class="col company">
    <h4>COMPANY</h4>
    <ul>
      <li><svg width="10" height="10" viewBox="0 0 10 10"><path d="M3 1l4 4-4 4" stroke="#2e9a3a" stroke-width="2" fill="none"/></svg>Home</li>
      <li><svg width="10" height="10" viewBox="0 0 10 10"><path d="M3 1l4 4-4 4" stroke="#2e9a3a" stroke-width="2" fill="none"/></svg>About Us</li>
      <li><svg width="10" height="10" viewBox="0 0 10 10"><path d="M3 1l4 4-4 4" stroke="#2e9a3a" stroke-width="2" fill="none"/></svg>What We Do</li>
      <li><svg width="10" height="10" viewBox="0 0 10 10"><path d="M3 1l4 4-4 4" stroke="#2e9a3a" stroke-width="2" fill="none"/></svg>Contact Us</li>
    </ul>
  </div>
  <div class="col contact">
    <h4>CONTACT US</h4>
    <ul>
      <li><svg width="13" height="13" viewBox="0 0 24 24"><path fill="#2e9a3a" d="M6.6 10.8a15.1 15.1 0 006.6 6.6l2.2-2.2a1 1 0 011-.25 11.4 11.4 0 003.6.6 1 1 0 011 1V20a1 1 0 01-1 1A17 17 0 013 4a1 1 0 011-1h3.5a1 1 0 011 1c0 1.25.2 2.45.6 3.6a1 1 0 01-.25 1z"/></svg>(555) 201-4486</li>
      <li><svg width="14" height="11" viewBox="0 0 24 18"><rect x="1" y="1" width="22" height="16" rx="2" fill="#2e9a3a"/><path d="M2 2l10 8 10-8" stroke="#fff" stroke-width="2" fill="none"/></svg>info@brellowcover.com</li>
      <li><svg width="12" height="15" viewBox="0 0 12 16"><path d="M6 0a6 6 0 016 6c0 4.5-6 10-6 10S0 10.5 0 6a6 6 0 016-6z" fill="#2e9a3a"/><circle cx="6" cy="6" r="2.2" fill="#fff"/></svg>803 Harbor Lane, Suite 12,<br>United States</li>
    </ul>
  </div>
  <div class="col news">
    <h4>JOIN NEWSLETTER</h4>
    <div class="news-form"><span>Email Address</span><b>JOIN NOW</b></div>
    <div class="socials"><span></span><span></span><span></span></div>
  </div>
</footer>
<div class="bottom">© 2025 <strong>BRELLOW COVER INSURANCE LP</strong> | All Rights Reserved</div>

</body>
</html>
```